Belmont Ridge Business Card Design Project

We have recently rebranded and would like to design new business cards that incorporate the corporate logo - double sided cards with corporate logo on one side and contact details on the other

Target Market(s)

Sophisticated and high net worth investors and finance industry professionals

Industry/Entity Type

Funds Management

Contact Information for Business Card

The card should prominently feature the company name and logo. Other details will be standard contact details for each staff member - name, address, phone, email, website

Colors
0054AA
0677BA
7BADD7
CADEEF
E8F1F8

Requirements
Must have
• Double-sided design with one side prominently featuring the corporate logo and the other side with all standard contact details

```html
<!DOCTYPE html>
<html lang="en">
<head>
<meta charset="utf-8">
<title>Belmont Ridge Business Card</title>
<link rel="stylesheet" href="https://fonts.googleapis.com/css2?family=Cinzel:wght@500&family=Lora:wght@400&display=swap">
<style>
  :root {
    --navy: #1f4372;
    --white: #ffffff;
    --ink: #555a60;
    --backdrop: #3a3a3c;
  }
  * { box-sizing: border-box; margin: 0; padding: 0; }
  html, body { width: 1200px; height: 689px; overflow: hidden; }
  body {
    background: var(--backdrop);
    position: relative;
    font-family: "Lora", Georgia, serif;
  }
  .card {
    position: absolute;
    top: 196px;
    width: 520px;
    height: 297px;
    overflow: hidden;
  }
  .card--contact { left: 50px; background: var(--white); }
  .card--brand { left: 630px; background: var(--navy); }

  .contact-stripe {
    position: absolute; top: 0; right: 0;
    width: 22px; height: 100%;
    background: var(--navy);
  }
  .contact-wordmark {
    position: absolute; left: 40px; top: 132px;
    font-family: "Cinzel", serif; font-weight: 500;
    font-size: 22px; letter-spacing: 1px;
    color: var(--navy);
  }
  .person {
    position: absolute; right: 50px; top: 52px;
    text-align: right;
  }
  .person-name {
    font-family: "Cinzel", serif; font-weight: 500;
    font-size: 25px; letter-spacing: 2px;
    color: var(--navy); line-height: 1.1;
  }
  .person-title {
    font-size: 12px; color: var(--ink); margin-top: 2px;
  }
  .details {
    position: absolute; right: 50px; top: 142px;
    list-style: none; text-align: right;
    font-size: 11.5px; color: var(--ink); line-height: 1.45;
  }
  .details li { display: flex; justify-content: flex-end; align-items: center; gap: 8px; }
  .details .block { display: block; }
  .details svg { width: 10px; height: 10px; fill: var(--navy); flex: none; }
  .details .spacer { height: 6px; }

  .brand-name {
    position: absolute; left: 0; right: 0; top: 112px;
    text-align: center;
    font-family: "Cinzel", serif; font-weight: 500;
    font-size: 46px; letter-spacing: 2px;
    color: var(--white);
  }
  .brand-url {
    position: absolute; left: 0; right: 0; top: 196px;
    text-align: center;
    font-size: 11px; letter-spacing: 4px;
    color: var(--white);
  }
</style>
</head>
<body>
  <section class="card card--contact" aria-label="Business card, contact side">
    <div class="contact-wordmark">Belmont Ridge</div>
    <div class="person">
      <div class="person-name">DANIEL HARTLEY</div>
      <div class="person-title">Founder &amp; CEO</div>
    </div>
    <ul class="details">
      <li><span><span class="block">418 Linden Avenue</span><span class="block">Westbrook, CT 06498</span></span>
        <svg viewBox="0 0 10 10"><path d="M5 0a3.5 3.5 0 0 0-3.5 3.5C1.5 6 5 10 5 10s3.5-4 3.5-6.5A3.5 3.5 0 0 0 5 0zm0 5a1.5 1.5 0 1 1 0-3 1.5 1.5 0 0 1 0 3z"/></svg></li>
      <li class="spacer"></li>
      <li>(555) 214-3870
        <svg viewBox="0 0 10 10"><path d="M2 0l2 2.5-1 1.2a6 6 0 0 0 3.3 3.3l1.2-1L10 8l-1.5 2C4 10 0 6 0 1.5z"/></svg></li>
      <li>(555) 214-3870
        <svg viewBox="0 0 10 10"><path d="M2.5 0h5v10h-5zM3.5 1v7h3V1z"/></svg></li>
      <li>info@belmontridge.com
        <svg viewBox="0 0 10 10"><path d="M0 2h10v6H0zm1 1v.3l4 2.5 4-2.5V3z"/></svg></li>
      <li>belmontridge.com
        <svg viewBox="0 0 10 10"><circle cx="5" cy="5" r="5"/></svg></li>
    </ul>
    <div class="contact-stripe"></div>
  </section>

  <section class="card card--brand" aria-label="Business card, brand side">
    <div class="brand-name">Belmont Ridge</div>
    <div class="brand-url">www.BelmontRidge.com</div>
  </section>
</body>
</html>
```